TA BRAMLEY BUSINESS CARD DESIGN PROJECT

We need to utilize our logo that was expertly created on PixelHarbor and now need to match this with a business card design.

```html
<!DOCTYPE html>
<html lang="en">
<head>
<meta charset="utf-8">
<title>TA BRAMLEY Business Card</title>
<link href="https://fonts.googleapis.com/css2?family=Montserrat:wght@400;700;800&display=swap" rel="stylesheet">
<style>
  :root {
    --brand-blue: #0f56a9;
    --ink: #171717;
    --paper: #ffffff;
    --backdrop: #d9cbb2;
    --text-dark: #2a2a2a;
  }
  * { margin: 0; padding: 0; box-sizing: border-box; }
  html, body { width: 1200px; height: 900px; overflow: hidden; }
  body {
    background: var(--backdrop);
    font-family: "Montserrat", sans-serif;
    position: relative;
  }
  .card {
    position: absolute;
    left: 310px;
    width: 582px;
    height: 331px;
    border-radius: 28px;
    overflow: hidden;
    box-shadow: 0 6px 14px rgba(0,0,0,0.25);
  }
  .card-front { top: 86px; background: var(--paper); }
  .card-back { top: 470px; background: var(--brand-blue); display: flex; align-items: center; justify-content: center; }

  .front-waves { position: absolute; inset: 0; width: 100%; height: 100%; }

  .brand-name {
    position: absolute;
    left: 26px;
    top: 48px;
    font-weight: 800;
    font-size: 40px;
    letter-spacing: 3px;
    color: var(--brand-blue);
    line-height: 1;
  }
  .brand-name-back {
    font-weight: 800;
    font-size: 66px;
    letter-spacing: 5px;
    color: var(--paper);
    line-height: 1;
  }

  .holder {
    position: absolute;
    right: 25px;
    top: 22px;
    text-align: right;
  }
  .holder-name { font-weight: 700; font-size: 22px; color: var(--brand-blue); line-height: 1.1; }
  .holder-role { font-weight: 400; font-size: 15px; color: var(--text-dark); letter-spacing: 0.5px; margin-top: 1px; }
  .accent-bar {
    position: absolute;
    right: 0;
    top: 25px;
    width: 13px;
    height: 37px;
    background: var(--brand-blue);
  }

  .address {
    position: absolute;
    right: 25px;
    top: 184px;
    text-align: right;
    color: var(--paper);
    font-size: 15.5px;
    line-height: 20px;
  }
  .contact-list {
    position: absolute;
    right: 25px;
    top: 245px;
    list-style: none;
    color: var(--paper);
    font-size: 15.5px;
    line-height: 20px;
  }
  .contact-list li { display: flex; align-items: center; justify-content: flex-end; gap: 6px; }
  .contact-icon { width: 12px; height: 12px; fill: var(--brand-blue); }
</style>
</head>
<body>
  <section class="card card-front">
    <svg class="front-waves" viewBox="0 0 862 490" preserveAspectRatio="none" aria-hidden="true">
      <path fill="var(--brand-blue)" d="M340 357 C520 285 660 212 750 210 C805 209 845 232 862 248 L862 262 C840 243 800 228 750 229 C660 232 520 300 340 357 Z"/>
      <path fill="var(--ink)" d="M0 347 C60 400 140 418 250 396 C420 362 620 240 745 236 C800 234 840 252 862 268 L862 490 L0 490 Z"/>
    </svg>

    <div class="brand-name">TA BRAMLEY</div>

    <div class="holder">
      <div class="holder-name">MARCUS ELLERY</div>
      <div class="holder-role">OWNER</div>
    </div>
    <div class="accent-bar"></div>

    <div class="address">
      <div>Your address, City</div>
      <div>State, Zip 1234</div>
    </div>

    <ul class="contact-list">
      <li>123 456 00000
        <svg class="contact-icon" viewBox="0 0 24 24"><path d="M6.6 10.8a15 15 0 0 0 6.6 6.6l2.2-2.2a1 1 0 0 1 1-.25 11.4 11.4 0 0 0 3.6.57 1 1 0 0 1 1 1V20a1 1 0 0 1-1 1A17 17 0 0 1 3 4a1 1 0 0 1 1-1h3.5a1 1 0 0 1 1 1c0 1.25.2 2.45.57 3.57a1 1 0 0 1-.25 1z"/></svg>
      </li>
      <li>info@yourmail.com
        <svg class="contact-icon" viewBox="0 0 24 24"><path d="M2 5h20v14H2z M2 5l10 7 10-7" /></svg>
      </li>
      <li>www.yourwebsite.com
        <svg class="contact-icon" viewBox="0 0 24 24"><circle cx="12" cy="12" r="10"/></svg>
      </li>
    </ul>
  </section>

  <section class="card card-back">
    <div class="brand-name-back">TA BRAMLEY</div>
  </section>
</body>
</html>
```